AUTOMOTIVE/ CAR REPAIRS / CRASH REPAIRS / PAINT SPRAYING AND PANEL BEATING

AUTOMOTIVE REPAIR. CAR / MOTORCYCLES GOT LOGO DESIGN / DID THINK ABOUT FACEBOOK DONT NOALREADY HAVE WEB ADRESS www.brenvashine.co.uk and mail sales@brenvashine,co.uk NEED SOMETHINK I CAN MANAGE TO UPLOAD PICTURES IN TO A GALLERY OR SOMETHINGLIKE THAT I ALSO SELL CAR AND MOTORCYCLES MAYBE A SELLS PAGE WITH A TILLWAVE LINK

Target Market(s)

TRADE / GENERAL PUBLIC

Industry/Entity Type

Automotive

Coding

Coded - Design and coding required

Number of Pages Required

4 page

Font styles to use
Serif
Sans Serif

Colors

Designer to choose colors to be used in the design.

Requirements
Must have
• GALLERY/ SHOP TO SALE CARS AND MOTORCYCLE / LOGOS OF MATERIALS I USE DORFLINT / KEBO / VASTINCO / Q WRAP / GLENBRUSH
• CONTACT US
Nice to have
• TILLWAVE / EASY TO MANAGE / VIDEO CLIP OF DORFLINT HUE PLANNER Z7
• SWIFT BLEND PAINT TONVIEW WETLINE AND TULVOKE

```html
<!DOCTYPE html>
<html lang="en">
<head>
<meta charset="utf-8">
<title>Brenvashine Bodyshop</title>
<link rel="stylesheet" href="https://fonts.googleapis.com/css2?family=Archivo:wght@500;600;700&family=Lato:wght@400;700&display=swap">
<style>
:root{
  --red:#b3121c;
  --red-bright:#d3141f;
  --dark:#1c1c1e;
  --ink:#2a2a2a;
  --grey-text:#555;
  --panel:#e6e6e7;
  --white:#fff;
  --head:'Archivo',Arial,sans-serif;
  --body:'Lato',Arial,sans-serif;
}
*{box-sizing:border-box;margin:0;padding:0}
html,body{width:1200px;height:4399px;overflow:hidden}
body{position:relative;background:var(--white);font-family:var(--body);color:var(--ink)}
.abs{position:absolute}
.center-text{text-align:center;left:0;width:1200px}
.section-title{font-family:var(--head);font-weight:600;font-size:34px;letter-spacing:.5px}
.section-title.red{color:var(--red)}
.section-title.dark{color:var(--ink)}
svg{display:block}

/* hero */
.hero{left:0;top:0;width:1200px;height:725px;background:linear-gradient(160deg,#3a3b3f 0%,#6d6e72 35%,#9a9b9f 55%,#4a4b4f 80%,#2a2b2e 100%)}
.hero-shade{left:0;top:0;width:1200px;height:725px;background:linear-gradient(90deg,rgba(0,0,0,.55),rgba(0,0,0,.1) 60%,rgba(0,0,0,.3))}
.brand{left:80px;top:36px;font-family:var(--head);font-weight:700;font-size:34px;color:var(--white);letter-spacing:3px}
.nav{top:54px;left:0;width:1200px;font-family:var(--head);font-weight:600;font-size:16px;color:var(--white)}
.nav a{position:absolute;color:inherit;text-decoration:none}
.nav a.active{color:var(--red-bright)}
.nav .phone{left:985px;top:-3px;display:flex;align-items:center;gap:6px;font-size:18px}
.hero-title{left:100px;top:258px;width:560px;text-align:center;font-family:var(--head);font-weight:700;font-size:50px;line-height:52px;color:var(--white)}
.hero-title span{color:#c9c9cb}
.hero-sub{left:100px;top:370px;width:560px;text-align:center;font-family:var(--head);font-weight:600;font-size:24px;color:var(--white)}
.btn-red{left:290px;top:421px;width:173px;height:43px;background:var(--red);color:var(--white);font-family:var(--head);font-weight:600;font-size:17px;display:flex;align-items:center;justify-content:center}
.hero-arrow{top:306px}

.emblem{width:56px;height:56px;border-radius:50%;background:var(--white);border:3px solid #d8d8d8;box-shadow:0 2px 6px rgba(0,0,0,.25)}

/* what we do */
.service{width:274px;height:274px;border-radius:50%;overflow:hidden;box-shadow:0 6px 14px rgba(0,0,0,.35)}
.service .label{position:absolute;left:0;width:100%;bottom:34px;text-align:center;color:var(--white);font-family:var(--head);font-weight:600;font-size:20px;line-height:22px}
.service.featured{background:var(--red)}
.service.featured .label{top:92px;bottom:auto}
.service.featured p{position:absolute;top:132px;left:36px;width:202px;text-align:center;color:var(--white);font-size:12px;line-height:17px}
.service .more{position:absolute;left:119px;top:218px;width:36px;height:36px;border-radius:50%;background:var(--white)}

/* about */
.about-heading{left:536px;top:1234px;font-family:var(--head);font-weight:600;font-size:35px;color:var(--ink)}
.about-text{left:536px;top:1290px;width:500px;font-size:18.5px;line-height:31px;color:#333}
.btn-outline{left:538px;top:1449px;width:176px;height:51px;border:2px solid var(--red);color:var(--red);font-family:var(--head);font-weight:600;font-size:17px;display:flex;align-items:center;justify-content:center}
.mark-disc{left:175px;top:1220px;width:300px;height:300px;border-radius:50%;background:radial-gradient(circle at 40% 35%,#fdfdfd,#d4d4d6);display:flex;align-items:center;justify-content:center;font-family:var(--head);font-weight:700;font-size:30px;color:var(--red);letter-spacing:2px}

/* why choose */
.why-bg{left:0;top:1640px;width:1200px;height:540px;background:linear-gradient(180deg,#fff 0%,#fff 55%,#e9e9ea 100%)}
.why-car{left:650px;top:1705px;width:550px;height:460px;border-radius:48% 40% 10% 30% / 40% 36% 10% 20%;background:linear-gradient(170deg,#eeeeef 0%,#b8b9bc 45%,#7e8084 75%,#3a3b3e 100%)}
.feature h3{position:absolute;left:34px;top:-3px;font-family:var(--head);font-weight:600;font-size:15.5px;color:var(--red);white-space:nowrap}
.feature p{position:absolute;left:34px;top:20px;width:400px;font-size:13.5px;line-height:19px;color:#333}

/* gallery */
.tile{position:absolute}
.partner{top:2810px;font-family:var(--head);font-weight:700;font-size:28px;white-space:nowrap;transform:translateX(-50%)}

/* products */
.products{left:0;top:2902px;width:1200px;height:480px;background:linear-gradient(180deg,#7a0d12 0%,#5b0e12 40%,#3a2a2c 75%,#2b2b2d 100%)}
.products h2{color:var(--white)}
.products-text{top:3037px;color:#f1f1f1;font-size:20px;line-height:31px}
.btn-ghost{left:517px;top:3120px;width:176px;height:51px;border:2px solid var(--white);color:var(--white);font-family:var(--head);font-weight:600;font-size:17px;display:flex;align-items:center;justify-content:center}

/* contact */
.contact-card{top:3416px;width:300px;text-align:center}
.contact-card .icon{width:150px;height:150px;margin:0 auto;border-radius:50%;border:7px solid var(--red);border-left-color:var(--dark);display:flex;align-items:center;justify-content:center;background:var(--white)}
.contact-card h4{margin-top:28px;font-family:var(--head);font-weight:600;font-size:19px;color:var(--red)}
.contact-card p{margin-top:6px;font-size:18.5px;line-height:31px;color:#444}
.contact-card p.big{font-size:21px;color:var(--ink)}

/* appointment */
.appointment{left:0;top:3721px;width:1200px;height:521px;background:var(--panel)}
.appt-address{top:3890px;font-family:var(--body);font-size:18px;line-height:31px;color:#444;letter-spacing:.3px}
.field{background:var(--white);border:1px solid #bdbdbd;font-size:18px;color:#555;padding-left:20px;display:flex;align-items:center}
.appt-note{top:4120px;font-size:20px;line-height:27px;color:#444}

/* footer */
.footer{left:0;top:4242px;width:1200px;height:157px;background:var(--dark)}
.footer-nav{top:4288px;left:162px;display:flex;gap:33px;font-family:var(--head);font-weight:600;font-size:16.5px;color:var(--white)}
.copyright{top:4325px;left:162px;font-size:13px;color:#ddd}
.social{top:4285px;width:30px;height:30px;border-radius:50%;background:#bdbdbf}
.pay-name{left:1000px;top:4286px;font-family:var(--head);font-weight:700;font-size:22px;color:var(--white);letter-spacing:1px}
</style>
</head>
<body>

<!-- HERO -->
<div class="abs hero" role="img" aria-label="Silver convertible sports car parked in a workshop"></div>
<div class="abs hero-shade"></div>
<div class="abs brand">BRENVASHINE</div>
<nav class="abs nav">
  <a class="active" style="left:423px">ABOUT US</a>
  <a style="left:543px">SERVICE</a>
  <a style="left:650px">CUSTOM</a>
  <a style="left:756px">GALLERY</a>
  <a style="left:867px">CONTACT</a>
  <a class="phone">
    <svg width="18" height="18" viewBox="0 0 24 24"><path fill="#fff" d="M6.6 10.8a15.1 15.1 0 0 0 6.6 6.6l2.2-2.2c.3-.3.7-.4 1-.2 1.1.4 2.3.6 3.6.6.6 0 1 .4 1 1V20c0 .6-.4 1-1 1A17 17 0 0 1 3 4c0-.6.4-1 1-1h3.5c.6 0 1 .4 1 1 0 1.3.2 2.5.6 3.6.1.3 0 .7-.2 1z"/></svg>
    0700 900 4125
  </a>
</nav>
<div class="abs hero-title">YOUR ONE STOP<br><span>BODY SHOP</span></div>
<div class="abs hero-sub">THE HOME OF PAINT PERFECTION</div>
<div class="abs btn-red">CONTACT US</div>
<svg class="abs hero-arrow" style="left:84px" width="30" height="60" viewBox="0 0 30 60"><path d="M26 4 4 30l22 26" fill="none" stroke="#fff" stroke-width="3"/></svg>
<svg class="abs hero-arrow" style="left:1084px" width="30" height="60" viewBox="0 0 30 60"><path d="M4 4l22 26L4 56" fill="none" stroke="#fff" stroke-width="3"/></svg>
<svg class="abs" style="left:0;top:600px" width="1200" height="126" viewBox="0 0 1200 126">
  <path d="M0 126 Q600 -40 1200 126 Z" fill="#fff"/>
  <path d="M110 104 Q600 -10 1090 104" fill="none" stroke="#b3121c" stroke-width="4"/>
</svg>
<div class="abs emblem" style="left:561px;top:614px"></div>

<!-- WHAT WE DO -->
<h2 class="abs center-text section-title red" style="top:695px">WHAT WE DO</h2>
<div class="abs service" style="left:80px;top:772px;background:radial-gradient(circle at 40% 30%,#8a7a55,#3b3327 55%,#141210)" role="img" aria-label="Car body under repair in the workshop">
  <div class="label">CAR BODY<br>REPAIRS</div>
</div>
<div class="abs service" style="left:332px;top:772px;background:radial-gradient(circle at 55% 45%,#6f8fc8,#2a4a8a 50%,#101830)" role="img" aria-label="Sprayer painting a motorcycle part">
  <div class="label">MOTORCYCLE<br>PAINTING</div>
</div>
<div class="abs service featured" style="left:590px;top:772px">
  <div class="label">WHEEL PAINTING</div>
  <p>ullamcorper est eget tempor cursus neque mi consectetuer mi a ultricies massa est sed nisl Class aptent taciti sociosqu ad litora</p>
  <div class="more"><svg width="36" height="36" viewBox="0 0 36 36"><path d="M11 15l7 7 7-7" fill="none" stroke="#b3121c" stroke-width="3"/></svg></div>
</div>
<div class="abs service" style="left:848px;top:772px;background:radial-gradient(circle at 50% 40%,#a8a9ac,#5d5e62 55%,#222)" role="img" aria-label="Grey saloon car front">
  <div class="label">IE CARS<br>AND BIKES</div>
</div>

<!-- ABOUT -->
<svg class="abs" style="left:0;top:1110px" width="1200" height="520" viewBox="0 0 1200 520">
  <path d="M0 100 Q600 -40 1200 100 L1200 420 Q600 560 0 420 Z" fill="#e6e6e7"/>
  <path d="M640 16 Q1000 20 1200 100 L1200 120 Q1000 40 640 16 Z" fill="#b3121c"/>
  <path d="M0 410 Q200 480 560 504 Q200 500 0 440 Z" fill="#b3121c"/>
</svg>
<div class="abs mark-disc">BRENVASHINE</div>
<h2 class="abs about-heading">BRENVASHINE BODYSHOP</h2>
<p class="abs about-text">Brenvashine, based in Ashbury, Norshire established in August, 1985 has grown to become Norshire's premiere manufacturer approved accident repair centre.&nbsp; Equipped with the latest technology and factory trained technicians</p>
<div class="abs btn-outline">READ MORE</div>

<!-- WHY CHOOSE US -->
<div class="abs why-bg"></div>
<h2 class="abs section-title dark" style="left:0;width:1212px;text-align:center;top:1665px">WHY CHOOSE US</h2>
<div class="abs why-car" role="img" aria-label="Silver hatchback car, three-quarter side view"></div>
<svg class="abs" style="left:0;top:1700px" width="1200" height="400" viewBox="0 1700 1200 400">
  <g fill="none" stroke="#777" stroke-width="1.2">
    <path d="M427 1755H725L819 1826"/>
    <path d="M435 1842H615L743 1895"/>
    <path d="M350 1953H615L654 1975"/>
    <path d="M461 2067H645"/>
  </g>
  <g fill="#b3121c">
    <circle cx="819" cy="1826" r="5"/><circle cx="743" cy="1895" r="5"/>
    <circle cx="654" cy="1975" r="5"/><circle cx="645" cy="2067" r="5"/>
  </g>
</svg>
<div class="abs feature" style="left:166px;top:1747px">
  <svg class="abs" style="left:0;top:0" width="28" height="28" viewBox="0 0 28 28"><circle cx="14" cy="14" r="12" fill="none" stroke="#b3121c" stroke-width="2"/><path d="M8 14l4 4 8-8" fill="none" stroke="#b3121c" stroke-width="2"/></svg>
  <h3>FULL OR PART RESPRAYS</h3>
  <p>Single panel resprays to full car resprays</p>
</div>
<div class="abs feature" style="left:166px;top:1834px">
  <svg class="abs" style="left:0;top:0" width="28" height="28" viewBox="0 0 28 28"><circle cx="14" cy="14" r="12" fill="none" stroke="#b3121c" stroke-width="2"/><path d="M8 14l4 4 8-8" fill="none" stroke="#b3121c" stroke-width="2"/></svg>
  <h3>DENT &amp; SCRATCH REMOVAL</h3>
  <p>From small paintless dent repairs to full panel replacements. Scratches, chips &amp; paint repairs undertaken</p>
</div>
<div class="abs feature" style="left:166px;top:1945px">
  <svg class="abs" style="left:0;top:0" width="28" height="28" viewBox="0 0 28 28"><circle cx="14" cy="14" r="12" fill="none" stroke="#b3121c" stroke-width="2"/><path d="M8 14l4 4 8-8" fill="none" stroke="#b3121c" stroke-width="2"/></svg>
  <h3>BUMPER REPAIR</h3>
  <p>Bumper scuffs, plastic bumper repairs and full bumper replacements. Full factory matched colours.</p>
</div>
<div class="abs feature" style="left:166px;top:2059px">
  <svg class="abs" style="left:0;top:0" width="28" height="28" viewBox="0 0 28 28"><circle cx="14" cy="14" r="12" fill="none" stroke="#b3121c" stroke-width="2"/><path d="M8 14l4 4 8-8" fill="none" stroke="#b3121c" stroke-width="2"/></svg>
  <h3>ALLOY WHEEL'S REFURBISHED</h3>
  <p>All accident repair undertaken. Just one call to Brenvashine and we'll help you take the first steps towards getting</p>
</div>
<svg class="abs" style="left:0;top:2170px" width="1200" height="110" viewBox="0 0 1200 110">
  <path d="M0 0 H1200 V10 Q600 170 0 10 Z" fill="#e9e9ea"/>
  <path d="M0 10 Q600 170 1200 10" fill="none" stroke="#b3121c" stroke-width="4"/>
</svg>
<div class="abs emblem" style="left:576px;top:2230px"></div>

<!-- GALLERY -->
<h2 class="abs section-title dark" style="left:0;width:1190px;text-align:center;top:2318px">OUR GALLERY</h2>
<div class="tile" style="left:160px;top:2395px;width:335px;height:365px;background:linear-gradient(160deg,#9aa4ad 0%,#c0303a 45%,#8e0f16 70%,#6b6e72 100%)" role="img" aria-label="Red classic car body stripped for respray"></div>
<div class="tile" style="left:507px;top:2395px;width:171px;height:176px;background:linear-gradient(170deg,#8c8f93,#c7c9cc 50%,#6e7175)" role="img" aria-label="Silver car bonnet after paint"></div>
<div class="tile" style="left:686px;top:2395px;width:354px;height:176px;background:linear-gradient(170deg,#5a5c60,#9c9ea2 45%,#3c3d40)" role="img" aria-label="Saloon car front in workshop"></div>
<div class="tile" style="left:507px;top:2583px;width:171px;height:177px;background:linear-gradient(170deg,#6d6a68,#9a2a30 60%,#4a1a1c)" role="img" aria-label="Classic car interior with steering wheel"></div>
<div class="tile" style="left:686px;top:2583px;width:173px;height:177px;background:linear-gradient(170deg,#8a8d91,#e8e8e8 50%,#5a5c60)" role="img" aria-label="White hatchback front after repair"></div>
<div class="tile" style="left:867px;top:2583px;width:173px;height:177px;background:linear-gradient(170deg,#b8bcc2,#2a2c30 55%,#111)" role="img" aria-label="Black hatchback in the spray booth"></div>
<div class="abs partner" style="left:300px;color:#c8102e">DORFLINT</div>
<div class="abs partner" style="left:466px;color:#222;font-size:24px">KEBO</div>
<div class="abs partner" style="left:625px;color:#1e4b8c;font-size:24px">VASTINCO</div>
<div class="abs partner" style="left:789px;color:#222;font-size:26px">Q WRAP</div>
<div class="abs partner" style="left:951px;color:#1f4fa0;font-size:22px">GLENBRUSH</div>

<!-- PRODUCTS -->
<div class="abs products" role="img" aria-label="Car interior dashboard in deep red tones"></div>
<h2 class="abs center-text section-title" style="top:2987px;color:#fff;left:3px">BUY OUR PRODUCTS</h2>
<p class="abs center-text products-text">Allamcorper est eget tempor cursus neque mi consectetuer mi a ultricies massa est<br>sed nisl Class aptent taciti sociosqu ad litora torquent per</p>
<div class="abs btn-ghost">SHOP NOW</div>
<svg class="abs" style="left:0;top:3230px" width="1200" height="153" viewBox="0 0 1200 153">
  <path d="M0 153 L0 145 Q600 -10 1200 145 L1200 153 Z" fill="#fff"/>
</svg>
<div class="abs emblem" style="left:569px;top:3237px"></div>

<!-- CONTACT -->
<h2 class="abs center-text section-title red" style="top:3337px;left:6px">CONTACT US</h2>
<div class="abs contact-card" style="left:154px">
  <div class="icon"><svg width="50" height="50" viewBox="0 0 24 24"><path d="M12 2a7 7 0 0 0-7 7c0 5 7 12 7 12s7-7 7-12a7 7 0 0 0-7-7zm0 9.5A2.5 2.5 0 1 1 12 6.5a2.5 2.5 0 0 1 0 5z" fill="none" stroke="#b3121c" stroke-width="1.3"/></svg></div>
  <h4>OUR ADDRESS</h4>
  <p>Brenvashine Bodyshop, Harlow Trade Park, Fenn Lane, Ashbury, Norshire, NR127QT</p>
</div>
<div class="abs contact-card" style="left:447px">
  <div class="icon"><svg width="50" height="50" viewBox="0 0 24 24"><path d="M6.6 10.8a15.1 15.1 0 0 0 6.6 6.6l2.2-2.2c.3-.3.7-.4 1-.2 1.1.4 2.3.6 3.6.6.6 0 1 .4 1 1V20c0 .6-.4 1-1 1A17 17 0 0 1 3 4c0-.6.4-1 1-1h3.5c.6 0 1 .4 1 1 0 1.3.2 2.5.6 3.6.1.3 0 .7-.2 1z" fill="none" stroke="#b3121c" stroke-width="1.3"/></svg></div>
  <h4>PHONE NUMBER</h4>
  <p class="big">0700 900 4125</p>
</div>
<div class="abs contact-card" style="left:741px">
  <div class="icon"><svg width="56" height="56" viewBox="0 0 24 24"><rect x="3" y="6" width="18" height="12" fill="none" stroke="#b3121c" stroke-width="1.2"/><path d="M3 6l9 7 9-7M3 18l7-6M21 18l-7-6" fill="none" stroke="#b3121c" stroke-width="1.2"/></svg></div>
  <h4>EMAIL ADDRESS</h4>
  <p>sales@brenvashine.co.uk</p>
</div>

<!-- APPOINTMENT -->
<div class="abs appointment"></div>
<svg class="abs" style="left:0;top:3721px" width="1200" height="100" viewBox="0 0 1200 100">
  <path d="M0 0 H1200 Q600 150 0 0 Z" fill="#fff"/>
  <path d="M0 0 Q600 150 1200 0" fill="none" stroke="#b3121c" stroke-width="4"/>
</svg>
<h2 class="abs center-text section-title red" style="top:3847px;left:-6px">MAKE AN APPOINTMENT</h2>
<p class="abs center-text appt-address">BRENVASHINE BODYSHOP, HARLOW TRADE PARK,<br>FENN LANE, ASHBURY, NORSHIRE, NR127QT</p>
<div class="abs field" style="left:271px;top:3979px;width:320px;height:51px">Date</div>
<div class="abs field" style="left:603px;top:3979px;width:319px;height:51px">Time</div>
<div class="abs field" style="left:273px;top:4044px;width:649px;height:51px">Price</div>
<p class="abs center-text appt-note" style="left:-3px">If you are unable to keep your appointment,<br>Please contact us as soon as possible</p>

<!-- FOOTER -->
<footer class="abs footer"></footer>
<div class="abs footer-nav"><span>HOME</span><span>ABOUT US</span><span>SERVICE</span><span>CUSTOM</span><span>GALLERY</span><span>CONTACT</span></div>
<div class="abs copyright">© 2019 Company Name&nbsp; All right reserved</div>
<div class="abs social" style="left:803px" aria-label="Social link"></div>
<div class="abs social" style="left:849px" aria-label="Social link"></div>
<div class="abs social" style="left:893px" aria-label="Social link"></div>
<div class="abs social" style="left:938px" aria-label="Social link"></div>
<div class="abs pay-name">TILLWAVE</div>

</body>
</html>
```